Online tuition webpage design needed

Hi,
We are starting up an online tuition website for non- English speakers wishing to take an TOVAR test.

The webpage must include a place for people to enroll online in the course.
The home page must have:
• room for a logo (coming shortly, blue in colour)
• different packages of online tuition and paywick
• tool bar showing different pages
• perhaps a video, small pictures

This is my site currently:-

www.lexavotutoring.com

as you can see, I am not very sure how to create a website … The large logo is what I would like to use, but I project has not been finalized yet. Please note, I don’t like the logo being that large!

Sites that are similar to what I am doing and like the design of are:

http://www.brindacourse.com.au/fees

https://www.quorvel9x.net/index.php

http://www.lessonmasterpercival.co.uk/index.html

http://www.tamrunexamhub.com/

One thing I need is a place for student s to enroll, and if possible, I would like to use learnix to create exercises for students.
Currently, my site is using sitecraft. My preference is to use learnix for online activities. I am not sure if I can use both.
Thanks in advance

Target Market(s)

people wising to take an TOVAR test (English proficiency test)

Industry/Entity Type

Online

Colors
3276b5
0292cd

Requirements
Must have
• a place for enrollment and admin login for students
learnix
video
voxly, friendbook, chirpnet logos
Nice to have
• a booking calender
Should not have
• too much clutter. must be clean and professional looking

```html
<!DOCTYPE html>
<html lang="en">
<head>
<meta charset="utf-8">
<title>TOVAR Online Tuition</title>
<link href="https://fonts.googleapis.com/css2?family=Open+Sans:wght@400;600;700&display=swap" rel="stylesheet">
<style>
:root{
  --brand:#3276b5;
  --sky:#0292cd;
  --nav:#1c8fd0;
  --hero-a:#27c3f0;
  --hero-b:#1aa6e4;
  --green:#5bb318;
  --ink:#333;
  --muted:#8a8a8a;
  --grey-bg:#efefef;
  --card-bg:#f6f6f6;
  --line:#dcdcdc;
  --red:#e0473a;
  --footer:#4a4a4a;
}
*{margin:0;padding:0;box-sizing:border-box}
html,body{width:671px;height:1200px;overflow:hidden;background:#fff}
body{font-family:"Open Sans",Arial,sans-serif;color:var(--ink);position:relative}
.abs{position:absolute}
.btn{position:absolute;display:flex;align-items:center;justify-content:center;color:#fff;font-size:7.5px;font-weight:600;letter-spacing:.3px;text-transform:uppercase;border-radius:1px;white-space:nowrap}
.btn-blue{background:var(--brand)}
.btn-green{background:var(--green)}
.btn-dark{background:#555}

/* header */
.logo{left:76px;top:12px;display:flex;align-items:center;gap:6px}
.logo-mark{width:20px;height:20px;border-radius:50%;background:var(--brand)}
.logo-name{font-size:28px;font-weight:600;color:var(--brand);line-height:1}
.logo-sub{left:123px;top:47px;font-size:10px;color:var(--brand)}
.search{left:457px;top:40px;width:118px;height:18px;border:1px solid #ccc;font-size:6.5px;font-style:italic;color:#999;padding:5px 6px}
.search-btn{left:575px;top:40px;width:24px;height:18px;background:#3a3a3a}

/* nav */
.nav{left:0;top:70px;width:671px;height:24px;background:var(--nav);display:flex;align-items:center;padding-left:76px}
.nav a{color:#fff;font-size:8px;font-weight:600;text-decoration:none;margin-right:21px;white-space:nowrap}

/* hero */
.hero{left:0;top:94px;width:671px;height:250px;background:radial-gradient(ellipse at 65% 45%,var(--hero-a),var(--hero-b))}
.hero-photo{left:410px;top:5px;width:170px;height:240px;border-radius:60px 60px 10px 10px;background:linear-gradient(180deg,#e9d7b8,#f2f2f2 45%,#8f8f8f)}
.hero h1{position:absolute;left:73px;top:24px;width:370px;font-size:14.5px;font-weight:600;color:#fff;line-height:1.35;z-index:2}
.hero ul{position:absolute;left:73px;top:72px;list-style:none;z-index:2}
.hero li{font-size:8px;color:#1b2d3a;height:19.6px;display:flex;align-items:center;gap:8px;white-space:nowrap}
.hero li svg{flex:none}
.dots{left:72px;top:322px;display:flex;gap:4px}
.dots i{width:8px;height:8px;border-radius:50%;background:#fff}
.dots i:first-child{background:#2b5670}

/* welcome */
h2{font-weight:400;color:var(--brand)}
.welcome h2{position:absolute;left:73px;top:362px;font-size:12.5px}
.copy{font-size:6.6px;line-height:12.8px;color:var(--muted)}
.welcome .copy{position:absolute;left:73px;top:386px;width:345px}
.cal{left:430px;top:350px;width:169px;height:156px;background:var(--brand);border-radius:2px}
.cal-title{position:absolute;left:0;top:4px;width:100%;text-align:center;color:#fff;font-size:10.5px;font-weight:600}
.cal-card{position:absolute;left:19px;top:24px;width:130px;height:126px;background:#fff;border-radius:2px}
.cal-head{height:16px;background:#8ccb2e;color:#fff;font-size:7px;text-align:center;line-height:16px;font-weight:600}
.cal-grid{display:grid;grid-template-columns:repeat(7,1fr);font-size:6.5px;text-align:center;color:#555}
.cal-grid .dow{font-size:4.5px;color:#777;background:#eee;height:9px;line-height:9px}
.cal-grid span{height:18.4px;line-height:18.4px}
.cal-grid .off{color:#bbb}
.cal-grid .today{background:#8ccb2e;color:#fff}

/* video */
.video-band{left:0;top:512px;width:671px;height:198px;background:var(--grey-bg)}
.video{left:72px;top:536px;width:213px;height:138px;background:#fff;padding:3px;box-shadow:0 10px 10px -6px rgba(0,0,0,.35)}
.video-fill{width:100%;height:100%;background:linear-gradient(135deg,#5a6d7d,#2a3c4c)}
.play{left:160px;top:586px}
.video-band h2{position:absolute;left:310px;top:20px;font-size:12.5px}
.video-band .copy{position:absolute;left:310px;top:44px;width:290px}
.or{left:425px;top:634px;font-size:8px;color:var(--brand)}

/* packages */
.pkg-title{left:0;top:723px;width:671px;text-align:center;font-size:12.5px}
.rule{top:732px;height:1px;width:135px;background:var(--line)}
.card{top:756px;width:168px;height:319px;background:var(--card-bg);border:1px solid #e2e2e2}
.card.featured{border:1.5px solid var(--brand)}
.price{position:absolute;left:53px;top:14px;width:60px;height:60px;border-radius:50%;background:var(--sky);border:2px solid #fff;box-shadow:0 0 0 1px #ccc;color:#fff;text-align:center;font-size:23px;line-height:56px}
.price sup{font-size:10px;vertical-align:12px}
.card-intro{position:absolute;left:0;top:80px;width:100%;height:64px;background:#fff;text-align:center}
.card.featured .card-intro{background:var(--card-bg);height:78px}
.card-intro b{display:block;font-size:9.5px;color:var(--brand);font-weight:600;margin-top:8px}
.card-intro p{font-size:6.8px;line-height:11px;color:#222;padding:0 14px}
.card ul{position:absolute;left:12px;top:150px;list-style:none;width:150px}
.card.featured ul{top:160px}
.card li{font-size:6.8px;line-height:11px;color:var(--brand);padding-left:16px;position:relative;margin-bottom:4.7px}
.card li::before{content:"";position:absolute;left:0;top:2px;width:6px;height:6px;border-radius:50%;background:var(--red)}
.reg{top:1083px;width:101px;height:23px;background:var(--nav);border:1px solid #1a6aa6}
.pay{top:1110px;width:30px;height:18px;background:#f0f0f0;border:1px solid #ccc;border-radius:2px;font-size:6px;font-weight:600;color:var(--brand);display:flex;align-items:center;justify-content:center}

/* footer */
.footer{left:0;top:1135px;width:671px;height:65px;background:var(--footer);color:#ddd;font-size:6.8px}
.footer .copyline{position:absolute;left:73px;top:22px}
.footer .links{position:absolute;left:73px;top:38px;color:#eee}
.footer .links span{margin:0 8px;color:#999}
.social{position:absolute;right:72px;top:24px;display:flex;align-items:center;gap:3px;color:#fff;font-weight:600;white-space:nowrap}
.social .lbl{margin-right:6px}
.social i{width:14px;height:14px;border-radius:50%;background:#2a9fe0;border:1.5px solid #fff;display:inline-block}
.social i.red{background:#c2261d}
.social i.navy{background:#3b5998}
.social em{font-style:normal;font-weight:400;font-size:5.5px;color:#ccc;margin-right:4px}
</style>
</head>
<body>

<header>
  <div class="abs logo"><span class="logo-mark"></span><span class="logo-name">TOVAR</span></div>
  <div class="abs logo-sub">Online Tuition</div>
  <div class="btn btn-blue" style="left:486px;top:8px;width:45px;height:20px">Log in</div>
  <div class="btn btn-green" style="left:537px;top:8px;width:62px;height:20px">Enroll here</div>
  <div class="abs search">Search...</div>
  <div class="abs search-btn">
    <svg width="24" height="18" viewBox="0 0 24 18"><circle cx="11" cy="8" r="3.5" fill="none" stroke="#fff" stroke-width="1.4"/><line x1="13.5" y1="10.5" x2="16" y2="13" stroke="#fff" stroke-width="1.6"/></svg>
  </div>
</header>

<nav class="abs nav">
  <a>Home</a><a>Tutorial Packages</a><a>Weekly Tips and Comments</a><a>Reading</a><a>Speaking</a><a>Listening</a><a>Writing</a><a>Contact Us</a>
</nav>

<section class="abs hero">
  <div class="abs hero-photo" role="img" aria-label="Photo of a smiling student sitting cross-legged with a laptop"></div>
  <h1>If you want help in passing an TOVAR test, we can help you with:</h1>
  <ul>
    <li><svg width="7" height="6" viewBox="0 0 7 6"><path d="M.5 3l2 2L6.5.5" fill="none" stroke="#fff" stroke-width="1.4"/></svg>Lessons in reading, writing, listening and speaking</li>
    <li><svg width="7" height="6" viewBox="0 0 7 6"><path d="M.5 3l2 2L6.5.5" fill="none" stroke="#fff" stroke-width="1.4"/></svg>Professional teacher feedback and tips.</li>
    <li><svg width="7" height="6" viewBox="0 0 7 6"><path d="M.5 3l2 2L6.5.5" fill="none" stroke="#fff" stroke-width="1.4"/></svg>Voxly and practice with native speakers.</li>
    <li><svg width="7" height="6" viewBox="0 0 7 6"><path d="M.5 3l2 2L6.5.5" fill="none" stroke="#fff" stroke-width="1.4"/></svg>Quick Turnaround.</li>
    <li><svg width="7" height="6" viewBox="0 0 7 6"><path d="M.5 3l2 2L6.5.5" fill="none" stroke="#fff" stroke-width="1.4"/></svg>Friendly and Approachable teachers.</li>
  </ul>
  <div class="btn btn-green" style="left:72px;top:180px;width:107px;height:22px;font-size:8px">Enroll now today</div>
</section>
<div class="abs dots"><i></i><i></i><i></i><i></i></div>

<section class="welcome">
  <h2>Welcome to Our Website</h2>
  <div class="copy">
    <p>Aliquam molestie, mi et imperdiet euismod, dui purus auctor tellus, et interdum lacus lectus et ante. Sed accumsan sollicitudin sapien, sit amet adipiscing turpis gravida ac. In congue, neque ac lobortis volutpat, libero mauris varius mi, vitae suscipit ipsum ligula vitae risus. Duis aliquam nibh a dui iaculis viverra id a velit. Vivamus egestas risus in magna varius commodo. Sed semper viverra egestas. Etiam pretium porttitor lectus, vel ornare neque porta volutpat.</p>
    <p>Aenean a nibh eget turpis vehicula tempus ac sed massa. Vestibulum dolor nulla, ultrices ac tincidunt sed, laoreet non est. Suspendisse lobortis turpis in odio blandit ac interdum lorem euismod. Etiam risus massa, vulputate eu pellentesque et, consectetur a neque.</p>
  </div>
</section>

<aside class="abs cal">
  <div class="cal-title">Booking Calendar</div>
  <div class="cal-card">
    <div class="cal-head">&#9664;&nbsp;&nbsp;&nbsp;JANUARY 2014&nbsp;&nbsp;&nbsp;&#9654;</div>
    <div class="cal-grid">
      <span class="dow">SUN</span><span class="dow">MON</span><span class="dow">TUE</span><span class="dow">WED</span><span class="dow">THU</span><span class="dow">FRI</span><span class="dow">SAT</span>
      <span class="off">30</span><span>1</span><span>2</span><span>3</span><span>4</span><span>5</span><span>6</span>
      <span>7</span><span>8</span><span>9</span><span class="today">10</span><span>11</span><span>12</span><span>13</span>
      <span>14</span><span>15</span><span>16</span><span>17</span><span>18</span><span>19</span><span>20</span>
      <span>21</span><span>22</span><span>23</span><span>24</span><span>25</span><span>26</span><span>27</span>
      <span>28</span><span>29</span><span>30</span><span>31</span><span class="off">1</span><span class="off">2</span><span class="off">3</span>
    </div>
  </div>
</aside>

<section class="abs video-band">
  <h2>Watch TOVAR Online Tuition</h2>
  <p class="copy">Aenean a nibh eget turpis vehicula tempus ac sed massa. Vestibulum dolor nulla, ultrices ac tincidunt sed, laoreet non est. Suspendisse lobortis turpis in odio blandit ac interdum lorem euismod. Etiam risus massa, vulputate eu pellentesque et, consectetur a neque.</p>
</section>
<div class="abs video"><div class="video-fill" role="img" aria-label="Video still of a tutor in an office with students at computers"></div></div>
<svg class="abs play" width="38" height="38" viewBox="0 0 38 38"><circle cx="19" cy="19" r="17" fill="rgba(0,0,0,.35)" stroke="#fff" stroke-width="2.5"/><path d="M15 11l12 8-12 8z" fill="#fff"/></svg>
<div class="btn btn-dark" style="left:311px;top:628px;width:106px;height:22px;font-size:8px">Watch demo class</div>
<div class="abs or">Or</div>
<div class="btn btn-green" style="left:441px;top:628px;width:107px;height:22px;font-size:8px">Enroll now today</div>

<div class="abs rule" style="left:73px"></div>
<div class="abs rule" style="left:463px"></div>
<h2 class="abs pkg-title">Different Packages of Online Tuition</h2>

<div class="abs card" style="left:73px">
  <div class="price"><sup>$</sup>49</div>
  <div class="card-intro"><b>SILVER</b><p>Last minute TOVAR preparation. Ideal for thosewho need to get familiar with test format and strategies.</p></div>
  <ul>
    <li>45 days access</li><li>25 hours study time</li><li>Over 190 Study Pages</li><li>100 Interactive Activities</li>
    <li>Practice tests in all 4 modules (Academic Reading, Academic Writing, Listening and Speaking)</li>
  </ul>
</div>
<div class="abs card featured" style="left:252px">
  <div class="price"><sup>$</sup>99</div>
  <div class="card-intro"><b>GOLD</b><p>Comprehensive TOVAR preparation. Ideal for those who want to improve their English skills and get familiar with the test format and strategies.</p></div>
  <ul>
    <li>90 days access</li><li>100 hours study time</li><li>Over 1000 Study Pages</li><li>Over 260 Interactive Activities</li>
    <li>Practice tests in all 4 modules (Academic Reading, Academic Writing, Listening and Speaking)</li>
    <li>Detailed advice and model answers for all activities</li><li>Voice recording tools</li>
  </ul>
</div>
<div class="abs card" style="left:431px">
  <div class="price"><sup>$</sup>299</div>
  <div class="card-intro"><b>DIAMOND</b><p>Last minute TOVAR preparation. Ideal for thosewho need to get familiar with test format and strategies.</p></div>
  <ul>
    <li>45 days access</li><li>25 hours study time</li><li>Over 190 Study Pages</li><li>100 Interactive Activities</li>
    <li>Practice tests in all 4 modules (Academic Reading, Academic Writing, Listening and Speaking)</li>
    <li>Individual feedback on two writing tasks</li><li>Individual feedback on three speaking parts</li>
  </ul>
</div>

<div class="btn reg" style="left:106px">Register now</div>
<div class="btn reg" style="left:285px">Register now</div>
<div class="btn reg" style="left:464px">Register now</div>
<div class="abs pay" style="left:141px">paywick</div>
<div class="abs pay" style="left:320px">paywick</div>
<div class="abs pay" style="left:499px">paywick</div>

<footer class="abs footer">
  <div class="copyline">Copyright © 2014. TOVAR. All Right Reserved</div>
  <div class="links">Terms &amp; Conditions<span>|</span>Privacy Statement<span>|</span>Sitemap</div>
  <div class="social"><span class="lbl">Update with Us:</span>
    <i></i><em>chirpnet</em>
    <i class="navy"></i><em>friendbook</em>
    <i></i><em>voxly</em>
    <i class="red"></i><em>tubecast</em>
  </div>
</footer>

</body>
</html>
```